Business Card Design Project

This is the first time we use our new logo. We need a business card that we can use both on our institutional corporate relationships and also that works for our staff that deals with consumers directly.

VELUNDA is a new company dedicated to empower consumers and to provide them with the best choices for specialized health care using the latest telemedicine technology (medicine at a distance via videoconference).

We want to print this cards in high quality materials and process. We will like designs that allow us to use UV spot varnish and other techniques that will differentiate us.

We are including Two different versions of Color logos. In addition we are including white over black background logos. Those can be used replacing the black for a color.

Please note this is the first time we will be creating any corporate materials with our new logo and colors.

Target Market(s)

34+ consumers of medium high and high socioeconomic levels.

Industry/Entity Type

Health

Requirements
Must have
• Our logo on its original colors
Should not have
• Any other graphical element or design that is not our logo

```html
<!DOCTYPE html>
<html lang="en">
<head>
<meta charset="utf-8">
<title>VELUNDA Business Card</title>
<link rel="stylesheet" href="https://fonts.googleapis.com/css2?family=Open+Sans:wght@700&family=Arimo:wght@400;700&display=swap">
<style>
  :root {
    --stage: #d8a56c;
    --card: #ffffff;
    --card-edge: #b88a58;
    --brand-blue: #1b5a82;
    --brand-teal: #2aa39a;
    --text-dark: #333333;
    --icon: #2b6f9a;
    --faint-disc: #e3edf6;
  }
  * { margin: 0; padding: 0; box-sizing: border-box; }
  html, body {
    width: 1200px;
    height: 364px;
    overflow: hidden;
    background: var(--stage);
  }
  .stage {
    position: relative;
    width: 1200px;
    height: 364px;
  }
  .card {
    position: absolute;
    top: 30px;
    width: 560px;
    height: 306px;
    background: var(--card);
    border: 1px solid var(--card-edge);
    overflow: hidden;
  }
  .card--front { left: 30px; }
  .card--back { left: 612px; width: 558px; }

  .faint-disc {
    position: absolute;
    right: -70px;
    top: 40px;
    width: 220px;
    height: 220px;
    border-radius: 50%;
    background: var(--faint-disc);
  }

  .brand {
    position: absolute;
    left: 44px;
    top: 66px;
    display: flex;
    align-items: center;
    gap: 18px;
  }
  .brand__dot {
    width: 58px;
    height: 58px;
    border-radius: 50%;
    background: var(--brand-teal);
  }
  .brand__name {
    font-family: "Open Sans", Arial, sans-serif;
    font-weight: 700;
    font-size: 40px;
    letter-spacing: 3px;
    color: var(--brand-blue);
    line-height: 1;
  }

  .person {
    position: absolute;
    left: 31px;
    top: 140px;
    font-family: "Arimo", Arial, sans-serif;
    line-height: 1;
  }
  .person__name {
    font-weight: 700;
    font-size: 19px;
    color: var(--brand-blue);
  }
  .person__title {
    font-weight: 400;
    font-size: 15px;
    color: var(--brand-teal);
  }

  .contact {
    position: absolute;
    left: 31px;
    top: 178px;
    list-style: none;
    font-family: "Arimo", Arial, sans-serif;
    font-size: 14px;
    color: var(--text-dark);
  }
  .contact__item {
    display: flex;
    align-items: center;
    gap: 6px;
    height: 20.5px;
  }
  .contact__icon {
    width: 12px;
    height: 12px;
    flex: none;
  }
  .address {
    position: absolute;
    left: 31px;
    top: 274px;
    font-family: "Arimo", Arial, sans-serif;
    font-size: 14px;
    color: var(--text-dark);
  }

  .back-name {
    position: absolute;
    right: 16px;
    top: 176px;
    font-family: "Open Sans", Arial, sans-serif;
    font-weight: 700;
    font-size: 60px;
    letter-spacing: 5px;
    color: var(--brand-blue);
    line-height: 1;
  }
  .back-web {
    position: absolute;
    left: 270px;
    top: 264px;
    font-family: "Arimo", Arial, sans-serif;
    font-size: 17px;
    letter-spacing: 3px;
    color: var(--text-dark);
  }
</style>
</head>
<body>
<main class="stage">
  <section class="card card--front">
    <div class="faint-disc"></div>

    <div class="brand">
      <span class="brand__dot"></span>
      <span class="brand__name">VELUNDA</span>
    </div>

    <p class="person">
      <span class="person__name">Your Name,</span>
      <span class="person__title">Title</span>
    </p>

    <ul class="contact">
      <li class="contact__item">
        <svg class="contact__icon" viewBox="0 0 12 12" aria-hidden="true">
          <circle cx="6" cy="6" r="5.5" fill="none" stroke="var(--icon)" stroke-width="1"/>
          <path d="M4 3.2 L5.2 4.6 L4.6 5.4 Q5.4 7 6.8 7.6 L7.5 7 L8.8 8.2 L8 9 Q5 8.6 3.2 4.2 Z" fill="var(--icon)"/>
        </svg>
        012-345-6789
      </li>
      <li class="contact__item">
        <svg class="contact__icon" viewBox="0 0 12 12" aria-hidden="true">
          <circle cx="6" cy="6" r="5.5" fill="none" stroke="var(--icon)" stroke-width="1"/>
          <path d="M4 3.2 L5.2 4.6 L4.6 5.4 Q5.4 7 6.8 7.6 L7.5 7 L8.8 8.2 L8 9 Q5 8.6 3.2 4.2 Z" fill="var(--icon)"/>
        </svg>
        012-345-6789
      </li>
      <li class="contact__item">
        <svg class="contact__icon" viewBox="0 0 12 12" aria-hidden="true">
          <rect x="0.5" y="2.5" width="11" height="7.5" rx="1" fill="var(--icon)"/>
          <path d="M1 3 L6 7 L11 3" fill="none" stroke="#ffffff" stroke-width="1"/>
        </svg>
        name@velunda.com
      </li>
      <li class="contact__item">
        <svg class="contact__icon" viewBox="0 0 12 12" aria-hidden="true">
          <circle cx="6" cy="6" r="5.2" fill="none" stroke="var(--icon)" stroke-width="1"/>
          <ellipse cx="6" cy="6" rx="2.2" ry="5.2" fill="none" stroke="var(--icon)" stroke-width="0.9"/>
          <path d="M0.8 6 H11.2 M1.8 3.5 H10.2 M1.8 8.5 H10.2" stroke="var(--icon)" stroke-width="0.9"/>
        </svg>
        www.velunda.com
      </li>
    </ul>

    <p class="address">Street Name, City Name, State, City Zip Code</p>
  </section>

  <section class="card card--back">
    <p class="back-name">VELUNDA</p>
    <p class="back-web">www.velunda.com</p>
  </section>
</main>
</body>
</html>
```